project - Misto Den

Dear designers, I'm Looking for an appealing new business card design to represent us for our new e-cigarette store: The MistO Den. Knowledgeable and friendly staff we aim for superior customer service with a positive atmosphere. Classic feel with modern touch is what we are aiming for . Lime green font and grey back round is the original color scheme but we are flexible and open to suggestions. I added some doodles to show you where my mind is at. address: 4827 203 St SW Edmonton, AB (inside the grand swap bazaar)web: themistoden.com email: info@themistoden.com phone : 555.214.6093 Thanks and am looking forward to seeing your creative , fresh and innovative designs.
Good luck everybody!
Gordon
Updates
lime green and charcoal grey please. thanks
Industry/Entity Type
Business
Logo Text
The MistO Den
Look and feel
Each slider illustrates characteristics of the customer's brand and the style your logo design should communicate.

```html
<!DOCTYPE html>
<html lang="en">
<head>
<meta charset="utf-8">
<title>The MistO Den — Business Card</title>
<link href="https://fonts.googleapis.com/css2?family=Ubuntu:wght@300;400&family=Dancing+Script:wght@400&display=swap" rel="stylesheet">
<style>
  :root {
    --backdrop: #d9d9d7;
    --charcoal: #1f2328;
    --lime: #b5e61d;
    --rule-grey: #6b6f74;
    --soft-grey: #8d9095;
  }
  html, body {
    margin: 0;
    padding: 0;
    width: 1200px;
    height: 1000px;
    overflow: hidden;
    background: var(--backdrop);
  }
  .canvas {
    position: relative;
    width: 1200px;
    height: 1000px;
  }
  .card {
    position: absolute;
    left: 250px;
    width: 700px;
    height: 400px;
    background: var(--charcoal);
    border-radius: 6px;
    box-shadow: 0 10px 30px rgba(0,0,0,0.25);
    overflow: hidden;
    font-family: "Ubuntu", sans-serif;
  }
  .card--front { top: 70px; }
  .card--back { top: 530px; }

  .rule {
    position: absolute;
    height: 2px;
    background: var(--rule-grey);
  }

  /* front */
  .card--front .rule { left: 90px; top: 120px; width: 200px; }
  .brand-name {
    position: absolute;
    left: 150px;
    top: 150px;
    margin: 0;
    font-weight: 400;
    font-size: 76px;
    letter-spacing: -1px;
    color: var(--lime);
    line-height: 1;
  }
  .tagline {
    position: absolute;
    left: 260px;
    top: 250px;
    margin: 0;
    font-family: "Dancing Script", cursive;
    font-size: 38px;
    color: var(--soft-grey);
    letter-spacing: 2px;
  }

  /* back */
  .back-name {
    position: absolute;
    left: 90px;
    top: 64px;
    margin: 0;
    font-weight: 400;
    font-size: 24px;
    color: var(--lime);
  }
  .card--back .rule { left: 120px; top: 120px; width: 200px; }
  .contact {
    position: absolute;
    left: 150px;
    top: 150px;
    margin: 0;
    font-style: normal;
    font-weight: 300;
    font-size: 23px;
    line-height: 1.45;
    color: var(--lime);
  }
</style>
</head>
<body>
<main class="canvas">
  <section class="card card--front" aria-label="Card front">
    <div class="rule"></div>
    <h1 class="brand-name">The MistO Den</h1>
    <p class="tagline">e-cigarette store</p>
  </section>

  <section class="card card--back" aria-label="Card back">
    <p class="back-name">The MistO Den</p>
    <div class="rule"></div>
    <address class="contact">
      4827 203 St SW Edmonton,<br>
      AB (inside the grand swap bazaar)<br>
      web: themistoden.com<br>
      email: info@themistoden.com<br>
      phone : 555.214.6093
    </address>
  </section>
</main>
</body>
</html>
```